Business card for my new company (Accounting firm)

I need a business card for my new business Brightwell Advisory and Ledger SA. Our services are accounting, tax, audit and financial management. Our customers are small companies, start-ups and new companies. The final design has to show financial security, trust and growth. Please find our logo attached to the business card. Text for the business card: Brightwell Advisory and Ledger SA Tomas Varenholt Director and Founder Certified Accountant Tel. 022 418 57 34 tv@clairevalconseil.ch www.clairevalconseil.ch Rue des Vergières 27 1201 Geneva
Target Market(s)
Our customers are small companies, start-ups and new companies.
Industry/Entity Type
Finance And Accounting
Contact Information for Business Card
Claireval Conseil et Comptes SA
Tomas Varenholt
Directeur et Fondateur
Expert-comptable diplômé
Tél. 022 418 57 34
tv@clairevalconseil.ch
www.clairevalconseil.ch
Rue des Vergières 27
1201 Genève

```html
<!DOCTYPE html>
<html lang="fr">
<head>
<meta charset="utf-8">
<title>Claireval Conseil et Comptes SA – Carte de visite</title>
<link rel="stylesheet" href="https://fonts.googleapis.com/css2?family=Lato:wght@400;700&display=swap">
<style>
  :root {
    --stage: #1c1c1e;
    --brand-blue: #1b6a9e;
    --sky-blue: #34aee3;
    --card-white: #ffffff;
    --ink-grey: #3a3a3c;
    --text-light: #ffffff;
  }
  * { box-sizing: border-box; margin: 0; padding: 0; }
  html, body {
    width: 1200px; height: 912px; overflow: hidden;
    background: var(--stage);
    font-family: "Lato", sans-serif;
  }
  .sheet {
    width: 1200px; height: 912px;
    display: flex; flex-direction: column; align-items: center; justify-content: center;
    gap: 40px;
  }
  .card {
    position: relative;
    width: 700px; height: 400px;
    overflow: hidden;
    box-shadow: 0 10px 30px rgba(0,0,0,.5);
  }

  /* Front side */
  .card--front { background: var(--brand-blue); color: var(--text-light); }
  .front-brand {
    position: absolute; left: 0; right: 0; top: 130px;
    display: flex; align-items: center; justify-content: center; gap: 16px;
  }
  .brand-square { width: 30px; height: 30px; background: var(--sky-blue); }
  .brand-name { font-weight: 700; font-size: 54px; letter-spacing: 1px; color: var(--text-light); }
  .front-web {
    position: absolute; left: 0; right: 0; top: 270px;
    text-align: center; font-size: 19px; letter-spacing: .3px;
  }

  /* Back side */
  .card--back { background: var(--brand-blue); }
  .back-shape { position: absolute; inset: 0; }
  .back-brand {
    position: absolute; left: 90px; top: 130px;
    display: flex; align-items: center; gap: 14px;
  }
  .back-brand .brand-name { color: var(--ink-grey); font-size: 50px; }
  .address {
    position: absolute; left: 70px; bottom: 16px;
    color: var(--text-light); font-size: 19px; line-height: 1.3; font-style: normal;
  }
  .contact {
    position: absolute; right: 34px; top: 120px;
    text-align: right; color: var(--text-light);
  }
  .contact-name { color: var(--sky-blue); font-weight: 700; font-size: 25px; margin-bottom: 4px; }
  .contact-role { font-size: 16px; line-height: 1.35; }
  .contact-lines { margin-top: 18px; font-size: 16px; line-height: 1.5; }
  .contact-line { display: flex; align-items: center; justify-content: flex-end; gap: 8px; }
  .contact-line svg { width: 14px; height: 14px; fill: var(--sky-blue); flex: none; }
</style>
</head>
<body>
<main class="sheet">

  <section class="card card--front" aria-label="Recto">
    <div class="front-brand">
      <span class="brand-square"></span>
      <span class="brand-name">Claireval</span>
    </div>
    <p class="front-web">www.clairevalconseil.ch</p>
  </section>

  <section class="card card--back" aria-label="Verso">
    <svg class="back-shape" viewBox="0 0 700 400" preserveAspectRatio="none">
      <path d="M0 0 H440 C465 140 360 285 0 300 Z" fill="var(--card-white)"/>
      <path d="M460 0 C486 110 438 210 358 262" fill="none" stroke="var(--sky-blue)" stroke-width="6"/>
    </svg>

    <div class="back-brand">
      <span class="brand-square"></span>
      <span class="brand-name">Claireval</span>
    </div>

    <address class="address">
      Claireval Conseil et Comptes SA<br>
      Rue des Vergières 27<br>
      1201 Genève
    </address>

    <div class="contact">
      <p class="contact-name">Tomas Varenholt</p>
      <p class="contact-role">Directeur et Fondateur<br>Expert-comptable diplômé</p>
      <div class="contact-lines">
        <p class="contact-line">022 418 57 34
          <svg viewBox="0 0 24 24" aria-hidden="true"><path d="M6.6 10.8a15.1 15.1 0 0 0 6.6 6.6l2.2-2.2c.3-.3.7-.4 1-.2 1.1.4 2.3.6 3.6.6.6 0 1 .4 1 1V20c0 .6-.4 1-1 1A17 17 0 0 1 3 4c0-.6.4-1 1-1h3.5c.6 0 1 .4 1 1 0 1.3.2 2.5.6 3.6.1.3 0 .7-.2 1z"/></svg>
        </p>
        <p class="contact-line">tv@clairevalconseil.ch
          <svg viewBox="0 0 24 24" aria-hidden="true"><path d="M2 5h20v14H2z M3.5 6.5 12 13l8.5-6.5" fill="var(--sky-blue)" stroke="var(--brand-blue)" stroke-width="1.5"/></svg>
        </p>
        <p class="contact-line">www.clairevalconseil.ch
          <svg viewBox="0 0 24 24" aria-hidden="true"><circle cx="12" cy="12" r="10"/><path d="M2 12h20M12 2c3 3 3 17 0 20M12 2c-3 3-3 17 0 20" fill="none" stroke="var(--brand-blue)" stroke-width="1.4"/></svg>
        </p>
      </div>
    </div>
  </section>

</main>
</body>
</html>
```